Animal Eye Clinic needs a Business card

We are a new veterinary ophthalmology practice (Ridgeline Pet Vision Care) and we need a business card designed. We only see animal eyes - we are not a regular veterinary clinic. We already have a logo. We are looking for a professional, good looking business card to hand out to our clients. We are looking for something simple but professional and contemporary. Our logo is likely the only picture/graphic that needs to be on the card.
Updates

Contact Information for Business Card

Delia Vossman, BSc, DVM, MSc, DipACVO
Veterinary Ophthalmologist

Phone: 250.418.3927
Email: ridgelinepetvisioncare@mailbox-example.net
Website: ridgelinepetvisioncare-example.net
Address: 1874 Thornbury Rd
Kelowna, BC, V1X 4M9

Colors

Designer to choose colors to be used in the design.

Requirements
Must have
• Our logo (attached)

```html
<!DOCTYPE html>
<html lang="en">
<head>
<meta charset="utf-8">
<title>Ridgeline Pet Vision Care – Business Card</title>
<link href="https://fonts.googleapis.com/css2?family=Lato:wght@400;700;900&display=swap" rel="stylesheet">
<style>
  :root {
    --teal: #1c9aab;
    --grey: #777878;
    --white: #ffffff;
    --stage: #2b2c2e;
  }
  * { margin: 0; padding: 0; box-sizing: border-box; }
  html, body {
    width: 1200px; height: 900px; overflow: hidden;
    background: var(--stage);
    font-family: "Lato", sans-serif;
  }
  .card {
    position: absolute;
    width: 540px; height: 310px;
    border-radius: 18px;
    overflow: hidden;
    box-shadow: 0 10px 24px rgba(0,0,0,.45);
  }
  .card svg.card-bg { position: absolute; inset: 0; width: 100%; height: 100%; }
  .card-front { left: 70px; top: 90px; background: var(--grey); }
  .card-back { left: 590px; top: 500px; background: var(--teal); }

  /* front */
  .front-brand {
    position: absolute; left: 245px; top: 118px;
    display: flex; align-items: center; gap: 14px;
  }
  .brand-dot {
    width: 46px; height: 46px; border-radius: 50%;
    background: var(--white); flex: none;
  }
  .brand-name {
    color: var(--white); font-weight: 900; font-size: 22px;
    line-height: 1.1; text-transform: uppercase; letter-spacing: .5px;
  }

  /* back */
  .back-brand {
    position: absolute; left: 385px; top: 62px; width: 140px;
    color: var(--teal); font-weight: 900; font-size: 17px;
    line-height: 1.15; text-align: center; text-transform: uppercase;
  }
  .person { position: absolute; left: 40px; top: 78px; color: var(--white); }
  .person-name { font-weight: 900; font-size: 32px; line-height: 1; }
  .person-creds { font-size: 9px; margin-top: 4px; letter-spacing: .2px; }
  .person-title { font-size: 15px; margin-top: 6px; }

  .clinic { position: absolute; left: 40px; top: 186px; color: var(--white); font-size: 14px; line-height: 1.2; }
  .clinic-name { font-weight: 700; }

  .contacts {
    position: absolute; left: 40px; top: 246px; list-style: none;
    color: var(--white); font-size: 12.5px; line-height: 1.35;
  }
  .contacts li { display: flex; align-items: center; gap: 8px; }
  .contacts svg { width: 12px; height: 12px; flex: none; }
</style>
</head>
<body>

<section class="card card-front" aria-label="Business card front">
  <svg class="card-bg" viewBox="0 0 540 310" aria-hidden="true">
    <path d="M205,310 C185,200 200,85 262,0 L540,0 L540,130 C470,235 330,300 205,310 Z" fill="var(--teal)"/>
  </svg>
  <div class="front-brand">
    <span class="brand-dot"></span>
    <span class="brand-name">Ridgeline Pet<br>Vision Care</span>
  </div>
</section>

<section class="card card-back" aria-label="Business card back">
  <svg class="card-bg" viewBox="0 0 540 310" aria-hidden="true">
    <path d="M335,0 C300,90 305,160 328,218 C425,230 500,195 540,150 L540,0 Z" fill="var(--grey)"/>
    <path d="M372,0 C345,70 345,132 362,182 C435,188 500,162 540,120 L540,0 Z" fill="var(--white)"/>
  </svg>
  <div class="back-brand">Ridgeline Pet Vision Care</div>

  <div class="person">
    <div class="person-name">Delia Vossman</div>
    <div class="person-creds">BSc, DVM, MSc, DipACVO</div>
    <div class="person-title">Veterinary Ophthalmologist</div>
  </div>

  <div class="clinic">
    <div class="clinic-name">Ridgeline Pet Vision Care</div>
    <div>1874 Thornbury Rd</div>
    <div>Kelowna, BC, V1X 4M9</div>
  </div>

  <ul class="contacts">
    <li>
      <svg viewBox="0 0 12 12" aria-hidden="true"><path d="M2.5,1 L4.5,1 L5.2,3.6 L4,4.5 C4.6,6 6,7.4 7.5,8 L8.4,6.8 L11,7.5 L11,9.5 C11,10.3 10.3,11 9.5,11 C5,11 1,7 1,2.5 C1,1.7 1.7,1 2.5,1 Z" fill="var(--white)"/></svg>
      250.418.3927
    </li>
    <li>
      <svg viewBox="0 0 12 12" aria-hidden="true"><rect x="0.5" y="2.5" width="11" height="7" fill="none" stroke="var(--white)"/><path d="M0.5,2.5 L6,7 L11.5,2.5" fill="none" stroke="var(--white)"/></svg>
      ridgelinepetvisioncare@mailbox-example.net
    </li>
    <li>
      <svg viewBox="0 0 12 12" aria-hidden="true"><circle cx="6" cy="6" r="5.2" fill="none" stroke="var(--white)"/><ellipse cx="6" cy="6" rx="2.2" ry="5.2" fill="none" stroke="var(--white)"/><path d="M0.8,6 L11.2,6" stroke="var(--white)"/></svg>
      www.ridgelinepetvisioncare-example.net
    </li>
  </ul>
</section>

</body>
</html>
```